Homemaking training schools needs a Business Card design

Designer, Hello!

No special requirements, good-looking enough.
--------------------------------------------------------------------------

Name: Marcus Dole
Chairman
Tel: 0574-71948263
Mobile: 13857420916
Email: kelvora@mailnest.example
Web: www.prt2019.example
Add: No.258, LanpingJie, BeiyuanQu, Ningbo, Zhejiang

LOGO
Ningbo PRT Homemaking Training School

Target Market(s)

pregnant women, mothers, infants, the elderly and families, including cleaning, cooking, nursing training.

Industry/Entity Type

Business

Contact Information for Business Card

Name: Marcus Dole
Chairman
Tel: 0574-71948263
Mobile: 13857420916
Email: kelvora@mailnest.example
Web: www.prt2019.example

LOGO

Font styles to use
Serif
Sans Serif
Decorative

Requirements
Nice to have
• Feels: clean, specifications, safety, comfort, warmth and happiness.

```html
<!DOCTYPE html>
<html lang="en">
<head>
<meta charset="utf-8">
<title>PeiRongTian Business Card</title>
<link rel="stylesheet" href="https://fonts.googleapis.com/css2?family=Montserrat:wght@300;400;600;700;800&display=swap">
<style>
  :root {
    --stage: #2a2a2c;
    --card: #050505;
    --blue: #1477c2;
    --pink: #ec1c8c;
    --white: #ffffff;
    --rule: #bdbdbd;
  }
  * { box-sizing: border-box; margin: 0; padding: 0; }
  html, body { width: 1200px; height: 900px; overflow: hidden; }
  body {
    background: var(--stage);
    font-family: "Montserrat", sans-serif;
    color: var(--white);
    position: relative;
  }
  .card {
    position: absolute;
    width: 540px;
    height: 310px;
    background: var(--card);
    border-radius: 22px;
    overflow: hidden;
  }
  .card--front { left: 80px; top: 110px; }
  .card--back { left: 580px; top: 480px; }

  /* front */
  .brand {
    position: absolute;
    left: 0; right: 0; top: 78px;
    display: flex; align-items: center; justify-content: center; gap: 14px;
  }
  .brand__dot { width: 22px; height: 22px; border-radius: 50%; background: var(--pink); }
  .brand__name { font-size: 50px; font-weight: 600; color: var(--blue); letter-spacing: 0.5px; }
  .tagline {
    position: absolute; left: 70px; right: 70px; top: 160px;
    display: flex; align-items: center; gap: 12px;
  }
  .tagline__rule { flex: 1; height: 1px; background: var(--rule); }
  .tagline__text { font-size: 19px; font-weight: 300; letter-spacing: 0.5px; }
  .front-web {
    position: absolute; left: 0; right: 0; top: 238px;
    text-align: center; font-size: 17px; font-weight: 700; color: var(--pink);
  }
  .front-web span { color: var(--white); }

  /* back */
  .back-band { position: absolute; inset: 0; }
  .back-mark {
    position: absolute; left: 92px; top: 78px;
    width: 56px; height: 56px; border-radius: 50%; background: var(--pink);
  }
  .divider {
    position: absolute; left: 200px; top: 52px;
    width: 1px; height: 160px; background: var(--rule);
  }
  .contact { position: absolute; left: 218px; top: 46px; }
  .contact__name { font-size: 24px; font-weight: 800; color: var(--pink); letter-spacing: 1px; line-height: 1.1; }
  .contact__role { font-size: 11px; font-weight: 700; letter-spacing: 0.5px; margin-bottom: 6px; }
  .contact__address { font-size: 11.5px; font-weight: 600; line-height: 1.35; margin-bottom: 5px; }
  .contact__list { list-style: none; }
  .contact__item {
    display: flex; align-items: center; gap: 7px;
    font-size: 11.5px; font-weight: 600; line-height: 1.45;
  }
  .contact__icon { width: 10px; height: 10px; flex: none; }
  .band-name {
    position: absolute; right: 36px; bottom: 24px;
    font-size: 34px; font-weight: 600; color: var(--white); letter-spacing: 0.5px;
  }
</style>
</head>
<body>

<section class="card card--front" aria-label="Card front">
  <div class="brand">
    <span class="brand__dot"></span>
    <span class="brand__name">PeiRongTian</span>
  </div>
  <div class="tagline">
    <span class="tagline__rule"></span>
    <span class="tagline__text">Training &amp; Services</span>
    <span class="tagline__rule"></span>
  </div>
  <p class="front-web">www.<span>prt2019</span>.example</p>
</section>

<section class="card card--back" aria-label="Card back">
  <svg class="back-band" width="540" height="310" viewBox="0 0 540 310" aria-hidden="true">
    <path d="M0,286 C200,266 400,226 540,176" fill="none" stroke="#ffffff" stroke-width="3"/>
    <path d="M0,298 C200,280 400,240 540,190 L540,310 L0,310 Z" fill="#1477c2"/>
  </svg>

  <div class="back-mark"></div>
  <div class="divider"></div>

  <div class="contact">
    <h1 class="contact__name">MARCUS DOLE</h1>
    <p class="contact__role">CHAIRMAN</p>
    <p class="contact__address">258, LanpingJie<br>BeiyuanQu, Ningbo, Zhejiang</p>
    <ul class="contact__list">
      <li class="contact__item">
        <svg class="contact__icon" viewBox="0 0 10 10"><path d="M2 1 L4 1 L4.6 3 L3.4 4 Q4.4 6 6 6.6 L7 5.4 L9 6 L9 8 Q8 9.2 6 8.6 Q2 7 1.2 3 Q1 1.6 2 1Z" fill="#ec1c8c"/></svg>
        0574-71948263
      </li>
      <li class="contact__item">
        <svg class="contact__icon" viewBox="0 0 10 10"><rect x="2.5" y="0.5" width="5" height="9" rx="1" fill="none" stroke="#ec1c8c" stroke-width="1.2"/><circle cx="5" cy="8" r="0.6" fill="#ec1c8c"/></svg>
        13857420916
      </li>
      <li class="contact__item">
        <svg class="contact__icon" viewBox="0 0 10 10"><rect x="0.6" y="2" width="8.8" height="6" fill="none" stroke="#ec1c8c" stroke-width="1.2"/><path d="M0.6 2 L5 5.5 L9.4 2" fill="none" stroke="#ec1c8c" stroke-width="1.1"/></svg>
        kelvora@mailnest.example
      </li>
      <li class="contact__item">
        <svg class="contact__icon" viewBox="0 0 10 10"><circle cx="5" cy="5" r="4.2" fill="none" stroke="#ec1c8c" stroke-width="1.1"/><ellipse cx="5" cy="5" rx="1.8" ry="4.2" fill="none" stroke="#ec1c8c" stroke-width="0.9"/><path d="M0.8 5 H9.2" stroke="#ec1c8c" stroke-width="0.9"/></svg>
        www.prt2019.example
      </li>
    </ul>
  </div>

  <p class="band-name">PeiRongTian</p>
</section>

</body>
</html>
```